Current website re-design to a updated look and feel.

We currently have a website www.brightlanefreight.com that we want to give an updated look and feel to. We are a logistics company that competes with Pellwick, Dm Harrowgate, Quill but on a smaller scale. We want something fresh and updated. We have two locations one in downtown Chicago, IL and one in Palatine IL. We are a fun group that also gets the job done. We know we need pictures of both locations and possibly a video, but we need fresh design ideas. The 'who we are' page is really the only page that we currently want to keep. The 'what we do' page needs to be completely re-done from a look and feel for sure.

Target Market(s)

Anyone who uses Truck transportation to move their product. Mainly US manufacturers.

Industry/Entity Type

Logistics

Number of Pages Required

5+ page

Font styles to use
Sans Serif

Colors
5c91c4
0355a3
d0dfed

Requirements
Must have
• The new design must entice people to want to do business with us. The design must have locations for pictures and at least one video which we know we will have to provide. Design must be easy to navigate.

```html
<!DOCTYPE html>
<html lang="en">
<head>
<meta charset="utf-8">
<title>Brightlane Freight</title>
<link href="https://fonts.googleapis.com/css2?family=Lato:ital,wght@0,400;0,700;0,900;1,400&display=swap" rel="stylesheet">
<style>
:root{
  --blue:#0355a3;
  --sky:#5c91c4;
  --mist:#d0dfed;
  --ink:#1c1c1c;
  --text:#444;
  --blush:#f1eaea;
  --panel:#f3f3f3;
  --footer:#262626;
  --white:#fff;
}
*{box-sizing:border-box;margin:0;padding:0}
html,body{width:1200px;height:3309px;overflow:hidden}
body{font-family:'Lato',sans-serif;color:var(--text);background:var(--white);position:relative}
.abs{position:absolute}
/* header */
.header{left:0;top:0;width:1200px;height:93px;background:var(--white)}
.brand{left:86px;top:22px;font-size:34px;font-weight:700;color:var(--blue);letter-spacing:-.5px}
.contact-bar{right:86px;top:32px;display:flex;align-items:center;gap:26px;font-size:15px;color:#333}
.contact-bar span{display:flex;align-items:center;gap:8px}
.dot{width:22px;height:22px;border-radius:50%;background:var(--sky);display:inline-flex;align-items:center;justify-content:center}
.login{background:var(--blue);color:#fff;padding:5px 16px;font-size:13px;border-radius:2px}
.nav{left:0;top:93px;width:1200px;height:48px;background:var(--sky)}
.nav a{position:absolute;top:0;color:#fff;text-decoration:none;font-size:17px;line-height:48px}
.nav .quote{background:var(--blue);left:893px;width:221px;text-align:center}
/* hero */
.hero{left:0;top:141px;width:1200px;height:446px;background:linear-gradient(180deg,#6d6a6f 0%,#c99a6c 28%,#4b4f57 55%,#2c2f36 100%)}
.hero h1{left:86px;top:160px;color:#fff;font-weight:900;line-height:.9;font-size:110px;letter-spacing:-1px}
.hero h1 small{display:block;font-size:60px;font-weight:900;margin-top:10px}
.play{left:560px;top:205px}
/* section titles */
.sec-title{width:1200px;left:0;text-align:center;font-size:36px;font-weight:700;color:var(--ink)}
.divider{left:468px;width:264px;height:30px}
/* service tiles */
.tile{top:765px;height:235px}
.tile-focus{display:flex;align-items:center;justify-content:center;background:#2b2b2b}
.tile-focus .box{width:200px;height:175px;background:var(--blue);opacity:.92;color:#fff;display:flex;flex-direction:column;align-items:center;justify-content:center;gap:16px;font-size:16px;font-weight:700}
/* founder */
.founder{left:0;top:1059px;width:1200px;height:538px;background:var(--blush)}
.founder-text{left:86px;top:198px;width:615px;font-size:12.5px;line-height:22px;color:#333}
.founder-text p{margin-bottom:22px}
.btn{left:86px;top:441px;width:126px;height:44px;background:var(--blue);color:#fff;font-size:13px;display:flex;align-items:center;justify-content:center;border-radius:2px}
.portrait{left:860px;top:88px;width:180px;height:450px;background:linear-gradient(180deg,#e8dfd8,#8a8170 45%,#2a2a2a);border-radius:90px 90px 0 0}
/* badges */
.awards{left:0;top:1597px;width:1200px;height:155px;background:var(--blue)}
.badge{top:18px;width:210px;height:121px;background:#fff;border-radius:3px;display:flex;align-items:center;justify-content:center}
/* testimonials */
.quote-card{top:1935px;width:497px;height:154px;border:2px solid #e2e2e2;background:#fff;padding:34px 28px;font-size:13px;font-style:italic;line-height:22px;color:#777}
.quote-card::after{content:"";position:absolute;left:110px;bottom:-14px;width:24px;height:24px;background:#fff;border-right:2px solid #e2e2e2;border-bottom:2px solid #e2e2e2;transform:rotate(45deg)}
.avatar{top:2112px;width:100px;height:100px;border-radius:50%;border:3px solid var(--mist)}
.client{top:2148px;font-size:18px;font-weight:700;color:var(--ink)}
.client small{font-size:12px;font-weight:400}
/* vision */
.vision{left:0;top:2294px;width:1200px;height:560px;background:linear-gradient(120deg,#4a5563 0%,#6d7784 40%,#3f4a58 70%,#56626f 100%)}
.vision .sec-title{color:#fff;top:72px}
.vcard{top:236px;width:494px;height:256px;background:#fff;border-radius:3px;padding:64px 26px 0;font-size:12.5px;line-height:20px;color:#555}
.vcard h3{color:var(--blue);font-size:17px;font-weight:700;margin-bottom:10px}
.vicon{width:110px;height:110px;border-radius:50%;background:#fff;top:180px;display:flex;align-items:center;justify-content:center}
/* footer */
.footer{left:0;top:2854px;width:1200px;height:455px;background:var(--footer)}
.updates{left:86px;top:2804px;width:1028px;height:145px;background:var(--panel);border-radius:2px}
.updates h4{position:absolute;left:92px;top:44px;font-size:18px;color:var(--ink);font-weight:700}
.updates p{position:absolute;left:92px;top:76px;font-size:13px;color:#444}
.subscribe{left:611px;top:48px;width:234px;height:51px;border:2px solid #ddd;background:#fff;color:var(--blue);font-weight:700;font-size:17px;display:flex;align-items:center;justify-content:center;gap:10px}
.foot-brand{left:86px;top:3072px;font-size:32px;color:#fff;font-weight:400}
.fcol{top:3027px;color:#ddd;font-size:13px;line-height:23px}
.fcol h5{color:#fff;font-size:17px;font-weight:700;letter-spacing:1px;margin:16px 0 14px}
.fbottom{left:86px;top:3243px;width:1028px;border-top:1px solid #444;padding-top:14px;display:flex;justify-content:space-between;font-size:12px;color:#bbb}
.fbottom nav span{margin:0 8px}
</style>
</head>
<body>

<header class="abs header">
  <div class="abs brand">Brightlane Freight</div>
  <div class="abs contact-bar">
    <span><i class="dot"><svg width="12" height="12" viewBox="0 0 24 24"><path fill="#fff" d="M6.6 10.8a15 15 0 006.6 6.6l2.2-2.2a1 1 0 011-.25 11 11 0 003.6.6 1 1 0 011 1V20a1 1 0 01-1 1A17 17 0 013 4a1 1 0 011-1h3.5a1 1 0 011 1 11 11 0 00.6 3.6 1 1 0 01-.25 1z"/></svg></i>555.010.4200</span>
    <span><i class="dot"><svg width="12" height="10" viewBox="0 0 24 18"><rect x="1" y="1" width="22" height="16" fill="none" stroke="#fff" stroke-width="2"/><path d="M1 1l11 9 11-9" fill="none" stroke="#fff" stroke-width="2"/></svg></i>info@brightlanefreight.com</span>
    <span class="login">Log in</span>
  </div>
</header>

<nav class="abs nav">
  <a style="left:88px">What We Do</a>
  <a style="left:249px">How We Do It</a>
  <a style="left:421px">Who We Are</a>
  <a style="left:582px">Tracking</a>
  <a style="left:713px">Chat</a>
  <a style="left:812px">Contact</a>
  <a class="quote">Request Quote</a>
</nav>

<section class="abs hero" role="img" aria-label="Video still of a highway at sunset with light trails between city buildings">
  <h1 class="abs">RELAX.<small>WE GOT THIS.</small></h1>
  <svg class="abs play" width="80" height="80" viewBox="0 0 80 80"><circle cx="40" cy="40" r="39" fill="#0355a3" opacity=".85"/><circle cx="40" cy="40" r="33" fill="none" stroke="#fff" stroke-opacity=".35"/><path d="M33 27l20 13-20 13z" fill="#fff"/></svg>
</section>

<h2 class="abs sec-title" style="top:642px">Your trusted logistic partner in worldwide</h2>
<svg class="abs divider" style="top:705px" viewBox="0 0 264 30"><line x1="0" y1="15" x2="110" y2="15" stroke="#333" stroke-width="2"/><line x1="154" y1="15" x2="264" y2="15" stroke="#333" stroke-width="2"/><circle cx="132" cy="15" r="13" fill="#5c91c4"/><path d="M119 15h26M132 2c-6 7-6 19 0 26M132 2c6 7 6 19 0 26" stroke="#fff" fill="none"/></svg>

<div class="abs tile" style="left:86px;width:252px;background:linear-gradient(180deg,#9aa4ad,#6b5a4c)" role="img" aria-label="Container port with cranes"></div>
<div class="abs tile tile-focus" style="left:346px;width:250px"><div class="box">TRANSPORTATION<svg width="14" height="14" viewBox="0 0 14 14"><rect width="14" height="14" fill="#fff"/><path d="M7 3v8M3 7h8" stroke="#0355a3" stroke-width="2"/></svg></div></div>
<div class="abs tile" style="left:604px;width:252px;background:linear-gradient(180deg,#e9e9ea,#c8b9a2)" role="img" aria-label="Warehouse interior with stacked boxes"></div>
<div class="abs tile" style="left:862px;width:252px;background:linear-gradient(180deg,#8fb0cf,#b2383a 60%,#5a5a5a)" role="img" aria-label="Red semi truck cab"></div>

<section class="abs founder">
  <h2 class="abs sec-title" style="top:60px">Welcome From Our Founder</h2>
  <svg class="abs divider" style="top:114px" viewBox="0 0 264 30"><line x1="0" y1="15" x2="110" y2="15" stroke="#333" stroke-width="2"/><line x1="154" y1="15" x2="264" y2="15" stroke="#333" stroke-width="2"/><circle cx="132" cy="15" r="13" fill="#5c91c4"/><path d="M119 15h26M132 2c-6 7-6 19 0 26M132 2c6 7 6 19 0 26" stroke="#fff" fill="none"/></svg>
  <div class="abs founder-text">
    <p>Brightlane Freight welcomes you to our growing family of clients! We have over 26 years of experience in helping people solve their logistics needs from coast-to-coast. We also provide friendly, exceptional service that makes it easy to do business with us. Give us a call today and experience the difference for yourself!</p>
    <p>"Our service commitment begins from the moment you contact us. We appreciate your trust, and we go the extra mile to ensure that your freight is handled with care and expediency. If an issue comes up, we work tirelessly to resolve it, staying in contact with you until your freight is delivered without issue!"</p>
    <p>Let us take the worry out of your logistics. Relax, we've got this! - Marian Holt, Founder</p>
  </div>
  <div class="abs btn">Read More</div>
  <div class="abs portrait" role="img" aria-label="Portrait of the founder standing with arms crossed"></div>
</section>

<section class="abs awards">
  <div class="abs badge" style="left:154px"><svg width="90" height="90"><circle cx="45" cy="45" r="42" fill="#1f3f7a"/></svg></div>
  <div class="abs badge" style="left:382px"><svg width="160" height="70"><rect x="5" y="5" width="36" height="60" fill="#1d5ea8"/><rect x="52" y="15" width="100" height="40" fill="#e6eef7"/></svg></div>
  <div class="abs badge" style="left:611px"><svg width="170" height="70"><rect x="5" y="5" width="60" height="60" fill="#222"/><rect x="75" y="20" width="90" height="30" fill="#ddd"/></svg></div>
  <div class="abs badge" style="left:838px"><svg width="180" height="90"><rect x="5" y="5" width="170" height="80" rx="6" fill="none" stroke="#2f8a7a" stroke-width="4"/></svg></div>
</section>

<h2 class="abs sec-title" style="top:1808px">Clients Say</h2>
<svg class="abs divider" style="top:1868px" viewBox="0 0 264 30"><line x1="0" y1="15" x2="110" y2="15" stroke="#333" stroke-width="2"/><line x1="154" y1="15" x2="264" y2="15" stroke="#333" stroke-width="2"/><circle cx="132" cy="15" r="13" fill="#5c91c4"/><path d="M119 15h26M132 2c-6 7-6 19 0 26M132 2c6 7 6 19 0 26" stroke="#fff" fill="none"/></svg>

<div class="abs quote-card" style="left:82px">"Lorem ipsum dolor sit amet, consectetur adipiscing elit, sed do eiusmod tempor incididunt ut labore et dolore magna aliqua. Ut enim ad minim veniam, quis nostrud exercitationopposed to using "</div>
<div class="abs quote-card" style="left:608px">"Lorem ipsum dolor sit amet, consectetur adipiscing elit, sed do eiusmod tempor incididunt ut labore et dolore magna aliqua. Ut enim ad minim veniam, quis nostrud exercitationopposed to using "</div>
<div class="abs avatar" style="left:155px;background:linear-gradient(180deg,#c9a28a,#7a4d3c)" role="img" aria-label="Client photo"></div>
<div class="abs client" style="left:276px">Dana R Whitfield, <small>New Jersey.</small></div>
<div class="abs avatar" style="left:680px;background:linear-gradient(180deg,#9fd3e6,#5aa7c4)" role="img" aria-label="Client photo"></div>
<div class="abs client" style="left:800px">Ellison, <small>New Jersey.</small></div>

<section class="abs vision" role="img" aria-label="Background of a hand pointing at a global logistics network over a port">
  <h2 class="abs sec-title">Brightlane Freight Vision And Mission</h2>
  <svg class="abs divider" style="top:128px" viewBox="0 0 264 30"><line x1="0" y1="15" x2="110" y2="15" stroke="#fff" stroke-width="2"/><line x1="154" y1="15" x2="264" y2="15" stroke="#fff" stroke-width="2"/><circle cx="132" cy="15" r="13" fill="#fff"/><path d="M119 15h26M132 2c-6 7-6 19 0 26M132 2c6 7 6 19 0 26" stroke="#5c91c4" fill="none"/></svg>
  <div class="abs vcard" style="left:86px"><h3>Brightlane Vision</h3>Brightlane vision is to be the premier third party logistics solution in North America. We will become premier by providing superior customer service, efficient and cost effective warehousing and distribution solutions.<br>The decisions we make today for hiring, training, technology, strategic services and customer satisfaction are based on this vision.</div>
  <div class="abs vcard" style="left:618px"><h3>Brightlane Vision</h3>Brightlane's mission is to provide the most thorough and satisfying third-party logistics experience for its customers. Brightlane uses leading technologies and an industry experienced staff to deliver an unparalleled customer service experience. Brightlane leverages the most efficient mode of transportation, and tailors cost effective solutions for warehousing and distribution of your products in every situation.</div>
  <div class="abs vicon" style="left:121px"><svg width="90" height="90" viewBox="0 0 90 90"><circle cx="45" cy="45" r="42" fill="#444"/><circle cx="45" cy="45" r="26" fill="none" stroke="#fff" stroke-width="5"/><circle cx="45" cy="45" r="13" fill="none" stroke="#fff" stroke-width="5"/><circle cx="45" cy="45" r="4" fill="#fff"/><path d="M45 45l24-24" stroke="#fff" stroke-width="4"/></svg></div>
  <div class="abs vicon" style="left:653px"><svg width="90" height="90" viewBox="0 0 90 90"><circle cx="45" cy="45" r="42" fill="#444"/><path d="M28 44a10 10 0 010-20 14 14 0 0127-4 10 10 0 019 24z" fill="#fff"/><path d="M45 44v30M38 52h14M38 60h14M38 68h14" stroke="#fff" stroke-width="3"/></svg></div>
</section>

<footer class="abs footer"></footer>
<div class="abs updates">
  <h4>GET UPDATES</h4>
  <p>Lorem Ipsum is simply dummy text of the printing and typesetting industry.</p>
  <div class="abs subscribe"><svg width="18" height="16" viewBox="0 0 24 22"><path d="M23 1L1 10l7 3 2 8 4-6 6 4z" fill="#0355a3"/></svg>SUBSCRIBE!</div>
</div>

<div class="abs foot-brand">Brightlane Freight</div>

<div class="abs fcol" style="left:401px">
  <svg width="36" height="48" viewBox="0 0 24 32"><path d="M12 0a12 12 0 00-12 12c0 9 12 20 12 20s12-11 12-20A12 12 0 0012 0zm0 17a5 5 0 110-10 5 5 0 010 10z" fill="#0355a3"/></svg>
  <h5>VISIT ME</h5>48 Orchard Row Suite 210<br>Alder Falls, OH 44000
</div>
<div class="abs fcol" style="left:620px">
  <svg width="48" height="48" viewBox="0 0 24 24"><path fill="#0355a3" d="M6.6 10.8a15 15 0 006.6 6.6l2.2-2.2a1 1 0 011-.25 11 11 0 003.6.6 1 1 0 011 1V20a1 1 0 01-1 1A17 17 0 013 4a1 1 0 011-1h3.5a1 1 0 011 1 11 11 0 00.6 3.6 1 1 0 01-.25 1z"/></svg>
  <h5>PHONE</h5>Office Phone: 555.010.4200<br>Warehouse: 555.010.4202<br>Fax: 555.010.4201
</div>
<div class="abs fcol" style="left:807px">
  <svg width="52" height="48" viewBox="0 0 26 24"><path d="M2 2h14v10H7l-4 3v-3H2z" fill="#0355a3"/><path d="M18 7h6v10h-1v3l-4-3h-8v-3h7z" fill="#0355a3"/></svg>
  <h5>LET'S TALK</h5>Rates: rates@brightlanefreight.com<br>Warehouse: warehouse@brightlanefreight.com<br>Information: info@brightlanefreight.com
</div>

<div class="abs fbottom">
  <nav>What We Do<span>|</span>How We Do It<span>|</span>Who We Are<span>|</span>Tracking<span>|</span>Chat<span>|</span>Contact</nav>
  <div>Copyright © 2017 Brightlane Freight. All rights reserved.</div>
</div>

</body>
</html>
```